Report template for evaluation reports to be used by non designers

We are looking for a report template that meets all the requirements listed in the attached documents. letter head, logo etc have been enclosed. Its important that the colour integrity is kept, but beyond that options are welcome.
Its important that the document is extremely easy to use and that is able to be adapted to include eatables, figures, pictures, text boxes etc and keep the integrity of the template

Target Market(s)

Governments, Civil society organisations and research institutions

Font styles to use
Sans Serif

Colors
6b449b
876aae
c0c0c0
000000

Requirements
Must have
• Clean, professional, not concluded, modern, must be easy to use
Should not have
• too busy, hard to use

```html
<!DOCTYPE html>
<html lang="en">
<head>
<meta charset="utf-8">
<title>Civic Insight Institute — Report Cover</title>
<link rel="stylesheet" href="https://fonts.googleapis.com/css2?family=Open+Sans:wght@400;600;700&display=swap">
<style>
  :root {
    --purple: #6b449b;
    --purple-light: #876aae;
    --silver: #c0c0c0;
    --ink: #000000;
    --text-grey: #6f6f6f;
    --map-grey: #e6e6e6;
    --ring-grey: #ededed;
    --paper: #ffffff;
    --backdrop: #e4e4e6;
  }
  * { box-sizing: border-box; margin: 0; padding: 0; }
  html, body {
    width: 1200px; height: 847px; overflow: hidden;
    background: var(--backdrop);
    font-family: "Open Sans", Arial, sans-serif;
  }
  .spread {
    position: absolute; left: 60px; top: 42px;
    width: 1080px; height: 764px;
    display: flex;
  }
  .page {
    position: relative; width: 540px; height: 764px;
    background: var(--paper);
    border-top: 6px solid var(--purple);
    border-bottom: 6px solid var(--purple);
    overflow: hidden;
  }
  .page--back {
    border-right: 1px solid #e2e2e2;
    background: linear-gradient(90deg, var(--paper) 82%, #f4f4f4);
  }

  /* wordmark */
  .wordmark {
    display: flex; align-items: center; gap: 10px;
    color: var(--ink); font-weight: 400;
    letter-spacing: 2px; text-transform: uppercase;
  }
  .wordmark__dot {
    width: 14px; height: 14px; border-radius: 50%;
    background: var(--purple);
  }

  /* back cover */
  .world-map {
    position: absolute; left: -20px; top: 70px;
    width: 600px; height: 360px;
    background: radial-gradient(ellipse 55% 50% at 50% 48%,
      var(--map-grey) 0%, var(--map-grey) 45%, rgba(230,230,230,0) 100%);
  }
  .page--back .wordmark {
    position: absolute; left: 0; right: 0; top: 520px;
    justify-content: center; font-size: 20px;
  }
  .contacts {
    position: absolute; left: 40px; right: 40px; top: 590px;
    display: flex; justify-content: space-between;
  }
  .contact {
    width: 150px; text-align: center;
    font-size: 9px; line-height: 1.5; color: var(--text-grey);
  }
  .contact__icon {
    width: 52px; height: 52px; border-radius: 50%;
    background: var(--purple); margin: 0 auto 12px;
    display: flex; align-items: center; justify-content: center;
  }
  .contact__icon--soft { background: var(--purple-light); }

  /* front cover */
  .cover-ring {
    position: absolute; left: 150px; top: 210px;
    width: 480px; height: 480px;
  }
  .page--front .wordmark {
    position: absolute; left: 36px; top: 34px; font-size: 20px;
  }
  .report-title {
    position: absolute; left: 36px; bottom: 58px;
    display: flex; align-items: center; gap: 26px;
  }
  .report-title h1 {
    color: var(--purple); font-weight: 700; font-size: 36px;
  }
</style>
</head>
<body>
<main class="spread">
  <section class="page page--back" aria-label="Back cover">
    <div class="world-map" role="img" aria-label="Faint grey world map"></div>

    <div class="wordmark"><span class="wordmark__dot"></span>Civic Insight Institute</div>

    <div class="contacts">
      <div class="contact">
        <div class="contact__icon contact__icon--soft">
          <svg width="22" height="22" viewBox="0 0 22 22" aria-hidden="true">
            <circle cx="11" cy="7" r="4" fill="#fff"/>
            <path d="M3 19c0-4.5 3.6-7 8-7s8 2.5 8 7z" fill="#fff"/>
          </svg>
        </div>
        +41700555012
      </div>
      <div class="contact">
        <div class="contact__icon">
          <svg width="22" height="22" viewBox="0 0 22 22" aria-hidden="true">
            <circle cx="12.5" cy="9" r="5" fill="none" stroke="#fff" stroke-width="2"/>
            <line x1="9" y1="12.5" x2="4" y2="18" stroke="#fff" stroke-width="2.4" stroke-linecap="round"/>
          </svg>
        </div>
        hello@civicinsight.org<br>www.civicinsight.org
      </div>
      <div class="contact">
        <div class="contact__icon">
          <svg width="22" height="22" viewBox="0 0 22 22" aria-hidden="true">
            <path d="M11 3 2 11h3v8h5v-5h2v5h5v-8h3z" fill="#fff"/>
          </svg>
        </div>
        0000 Sample Lane,<br>Harbour View, NZ00000
      </div>
    </div>
  </section>

  <section class="page page--front" aria-label="Front cover">
    <svg class="cover-ring" viewBox="0 0 480 480" aria-hidden="true">
      <circle cx="240" cy="240" r="200" fill="none" stroke="var(--ring-grey)" stroke-width="64"/>
    </svg>

    <div class="wordmark"><span class="wordmark__dot"></span>Civic Insight Institute</div>

    <div class="report-title">
      <svg width="40" height="34" viewBox="0 0 40 34" aria-hidden="true">
        <polygon points="0,0 40,17 0,34" fill="var(--purple)"/>
        <polygon points="0,17 20,17 0,34" fill="var(--purple-light)"/>
      </svg>
      <h1>Report Title</h1>
    </div>
  </section>
</main>
</body>
</html>
```